Plakate für Haushaltshilfen und Alltagsbegleiter
Zielgruppe
Wir bieten haushaltsnahe Dienstleistungen (Haushaltshilfen und Altgasbegleiter) für Personen mit einem Pflegegrad 1 - 5 an.
Zielgruppe sind Personen mit einem Pflegegrad 1 - 5. Hauptsächlich ältere Menschen die Unterstützung/Betreuung im Alltag und Haushalt benötigen.
Aufgabenstellung
Wir benötigen für unsere Büroräume eine Fensterbeschriftung. Es handelt sich hier um 5 Fenster (Glasflächen) und eine Glastür. Die Vorgabe ist, dass von außen zu erkennen ist dass sich um alle Räumlichkeiten um unsere (Firma Lindwerk) Räumlichkeiten handelt. Desweiteren soll auch unser Angebot erkennbar sein.
Unser Angebot enthält: Haushaltshilfen und Alltagsbegleiter
- kostenlose Haushaltshilfe ab Pflegegrad 1
- Abrechnung mit allen Kostenträgern
Da wir keine Schilder an die Fassade anbringen können, müßen die Glasflächen dafür genutzt werden um zum Einen uns als Firma erkennbar zu machen und zum anderen unser Angebot kurz zu präsentieren.
Uns ist wichtig dass unser Logo verwendet wir und auch unsere Farben.
Desweiteren sollten an den Fenstern auch teilweise eine Sichtschutz nach innen, angebracht werden, aber eben nur teilweise also nicht das ganzen Fenster z.Bsp. mit einer Blickdichten Folie überziehen, sondern in Augenhöhe wenn Fußgänger vorbei laufen.

```html
<!DOCTYPE html>
<html lang="de">
<head>
<meta charset="utf-8">
<title>Lindwerk – Fensterbeschriftung</title>
<link href="https://fonts.googleapis.com/css2?family=Montserrat:wght@400;500;600;700;800&display=swap" rel="stylesheet">
<style>
  :root{
    --red:#b3252d;
    --red-dark:#8e1c22;
    --ink:#2a2a2b;
    --white:#ffffff;
    --paper:#f4f4f4;
    --stage:#b3b3b3;
    --glass:#a8a8a8;
    --text:#333333;
  }
  *{box-sizing:border-box;margin:0;padding:0}
  html,body{width:1200px;height:813px;overflow:hidden;background:var(--stage)}
  body{position:relative;font-family:"Montserrat",sans-serif;color:var(--text)}

  .panel{position:absolute;overflow:hidden;background:var(--white)}
  .panel svg.shape{position:absolute;left:0;width:100%;display:block}

  .brand{position:absolute;left:0;width:100%;text-align:center}
  .brand__dot{display:block;width:26px;height:26px;border-radius:50%;border:3px solid var(--red);margin:0 auto 4px}
  .brand__name{font-weight:700;font-size:15px;letter-spacing:.06em;color:var(--red);text-transform:uppercase}
  .brand--right{text-align:right;right:16px;left:auto;width:auto}
  .brand--right .brand__dot{margin:0 8px 4px auto}

  .headline{position:absolute;font-weight:800;color:var(--red);text-transform:uppercase;line-height:1.2}

  .photo{position:absolute}
  .tag{position:absolute;background:var(--red);color:var(--white);font-weight:800;text-transform:uppercase;
       text-align:center;line-height:1.15;border-radius:6px;padding:5px 10px;box-shadow:0 2px 4px rgba(0,0,0,.3)}

  /* Poster: Vorteile */
  .p-vorteile{left:192px;top:12px;width:258px;height:351px}
  .p-vorteile .band{position:absolute;top:93px;left:0;width:100%;height:24px;background:var(--ink);
       color:var(--white);font-weight:800;font-size:15px;text-align:center;line-height:24px}
  .benefit{position:absolute;width:110px;text-align:center;font-size:7.4px;line-height:1.3;color:var(--text)}
  .benefit__icon{width:40px;height:40px;margin:0 auto 5px;border-radius:5px;background:var(--red);
       color:var(--white);font-weight:700;font-size:20px;line-height:40px}

  /* Poster: Angebot */
  .p-angebot{left:470px;top:12px;width:258px;height:351px}
  /* Poster: Pflegegrad */
  .p-pflegegrad{left:748px;top:12px;width:258px;height:351px;background:var(--paper)}

  /* Glastür */
  .p-tuer{left:270px;top:377px;width:184px;height:412px;background:var(--glass);border:1px solid var(--ink)}
  .p-tuer .brand__name{color:var(--white)}
  .p-tuer .brand__dot{border-color:var(--white)}
  .door-copy{position:absolute;left:18px;top:176px;width:140px;color:var(--white);font-weight:700;
       font-size:8.3px;line-height:1.38;text-transform:uppercase}

  /* Poster: Leistungen */
  .p-leistungen{left:474px;top:377px;width:218px;height:351px}
  .intro{position:absolute;left:12px;top:88px;width:194px;text-align:center;color:var(--red);
       font-weight:600;font-size:9.4px;line-height:1.3}
  .tv{position:absolute;background:#000;color:var(--white);font-weight:400;font-size:20px;
       display:flex;align-items:center;justify-content:center}
  .service-band{position:absolute;left:0;top:199px;width:100%;height:20px;background:var(--red);
       color:var(--white);font-weight:800;font-size:10px;text-align:center;line-height:20px}
  .service{position:absolute;width:72px;text-align:center;font-size:5px;font-weight:700;text-transform:uppercase;color:var(--ink)}
  .service svg{display:block;margin:0 auto 5px;width:28px;height:28px}

  /* Poster: Termin */
  .p-termin{left:712px;top:377px;width:218px;height:351px}
  .cta{position:absolute;left:0;top:201px;width:100%;text-align:center;font-size:11.5px;color:var(--ink)}
  .phone{position:absolute;left:18px;top:222px;width:182px;height:26px;border-radius:8px;background:var(--red);
       color:var(--white);font-weight:800;font-size:18px;text-align:center;line-height:26px;letter-spacing:.03em}
  .url{position:absolute;left:0;top:256px;width:100%;text-align:center;font-weight:800;font-size:16px;color:var(--ink)}

  .glass-note{position:absolute;left:474px;top:760px;font-size:19px;color:var(--white)}
  .glass-line{position:absolute;left:0;top:0}
</style>
</head>
<body>

<!-- Vorteile -->
<section class="panel p-vorteile">
  <div class="brand" style="top:16px"><span class="brand__dot"></span><span class="brand__name">Lindwerk</span></div>
  <div class="band">UNSERE VORTEILE</div>
  <div class="benefit" style="left:12px;top:127px"><div class="benefit__icon">$</div>Abrechnung mit allen Pflegekassen möglich</div>
  <div class="benefit" style="left:130px;top:127px"><div class="benefit__icon">+</div>Abrechnung über den Entlastungsbetrag von mind. 125 € mtl. ab Pflegegrad 1 möglich</div>
  <div class="benefit" style="left:12px;top:213px"><div class="benefit__icon">♥</div>Auch über die Verhinderungspflege</div>
  <div class="benefit" style="left:130px;top:213px"><div class="benefit__icon">✎</div>Hilfe bei der Antragsstellung</div>
  <svg class="shape" style="bottom:0;height:100px" viewBox="0 0 258 100" preserveAspectRatio="none">
    <polygon points="0,36 110,78 0,100" fill="var(--red)"/>
    <polygon points="90,100 258,10 258,100" fill="var(--red)"/>
    <polygon points="150,100 258,50 258,100" fill="var(--ink)"/>
  </svg>
</section>

<!-- Angebot -->
<section class="panel p-angebot">
  <div class="photo" role="img" aria-label="Foto eines lachenden älteren Paares" style="left:0;top:150px;width:100%;height:201px;background:linear-gradient(160deg,#e7e7e7,#c9bdb5 50%,#5a5f66)"></div>
  <svg class="shape" style="top:0;height:110px" viewBox="0 0 258 110" preserveAspectRatio="none">
    <polygon points="0,0 180,0 0,108" fill="var(--red)"/>
    <polygon points="150,0 258,0 258,40" fill="var(--ink)"/>
    <polygon points="170,0 190,0 20,102 0,108" fill="var(--red-dark)" opacity=".6"/>
  </svg>
  <div class="brand brand--right" style="top:28px"><span class="brand__dot"></span><span class="brand__name">Lindwerk</span></div>
  <h2 class="headline" style="right:20px;top:100px;width:220px;text-align:right;font-size:11.6px">Wir bieten Haushaltshilfen und Alltagsbegleiter für Privathaushalte an.</h2>
  <div class="tag" style="left:122px;top:282px;width:118px;font-size:8.5px;transform:rotate(-8deg)">Abrechnung mit allen Kostenträgern</div>
</section>

<!-- Pflegegrad -->
<section class="panel p-pflegegrad">
  <div class="brand" style="top:28px"><span class="brand__dot"></span><span class="brand__name">Lindwerk</span></div>
  <h2 class="headline" style="left:0;top:100px;width:100%;text-align:center;font-size:11.8px">Haushaltshilfen und<br>Alltagsbegleiter</h2>
  <div class="photo" role="img" aria-label="Foto einer Familie mit Großvater, Mutter und Kind" style="left:0;top:132px;width:100%;height:219px;background:linear-gradient(150deg,#eef0f3,#d9c6b8 45%,#8aa3c7 75%,#c9ccd2)"></div>
  <div class="tag" style="left:10px;top:154px;width:112px;font-size:8px;text-align:left;transform:rotate(5deg)">Kostenlose Haushaltshilfe ab Pflegegrad 1</div>
  <svg class="shape" style="bottom:0;height:95px" viewBox="0 0 258 95" preserveAspectRatio="none">
    <polygon points="0,40 90,95 0,95" fill="var(--red)"/>
    <polygon points="80,95 258,5 258,95" fill="var(--red)"/>
    <polygon points="140,95 258,45 258,95" fill="var(--ink)"/>
  </svg>
</section>

<!-- Glastür -->
<section class="panel p-tuer">
  <svg class="shape" style="top:0;height:95px" viewBox="0 0 184 95" preserveAspectRatio="none">
    <polygon points="0,0 150,0 0,90" fill="var(--red)"/>
    <polygon points="130,0 145,0 0,88 0,80" fill="var(--red-dark)" opacity=".6"/>
  </svg>
  <div class="brand" style="top:112px"><span class="brand__dot"></span><span class="brand__name">Lindwerk</span></div>
  <p class="door-copy">Den Alltag zu bewältigen kann eine echte Herausforderung sein. Egal ob Sie Hilfe beim Einkaufen oder anderen alltäglichen Aktivitäten benötigen, wir helfen gerne.</p>
</section>

<!-- Leistungen -->
<section class="panel p-leistungen">
  <svg class="shape" style="top:0;height:95px" viewBox="0 0 218 95" preserveAspectRatio="none">
    <polygon points="0,0 170,0 0,92" fill="var(--red)"/>
    <polygon points="140,0 218,0 218,28" fill="var(--ink)"/>
  </svg>
  <div class="brand brand--right" style="top:20px"><span class="brand__dot"></span><span class="brand__name">Lindwerk</span></div>
  <p class="intro">Egal ob Sie Hilfe beim Einkaufen oder anderen alltäglichen Aktivitäten benötigen, wir helfen gerne.</p>
  <div class="tv" style="left:61px;top:138px;width:78px;height:56px">TV</div>
  <div class="service-band">UNSERE LEISTUNGEN</div>
  <div class="service" style="left:5px;top:235px"><svg viewBox="0 0 28 28" fill="none" stroke="var(--red)" stroke-width="1.6"><path d="M6 3v19M3 22h10M16 12h8l-1 10h-6z"/></svg>Haushaltshilfe</div>
  <div class="service" style="left:73px;top:235px"><svg viewBox="0 0 28 28" fill="none" stroke="var(--red)" stroke-width="1.6"><path d="M7 8h14l1 17H6z"/><path d="M11 8V5h6v3"/></svg>Einkaufsservice</div>
  <div class="service" style="left:141px;top:235px"><svg viewBox="0 0 28 28" fill="none" stroke="var(--red)" stroke-width="1.6"><path d="M22 3L14 17M10 16l7 4-3 5-9-3z"/></svg>Kehrwoche</div>
  <div class="service" style="left:5px;top:290px"><svg viewBox="0 0 28 28" fill="none" stroke="var(--red)" stroke-width="1.6"><path d="M8 6l14 14M18 10l-6 6M5 5l2 2M4 12h3M12 3v3"/></svg>Fensterreinigung</div>
  <div class="service" style="left:73px;top:290px"><svg viewBox="0 0 28 28" fill="none" stroke="var(--red)" stroke-width="1.6"><rect x="5" y="3" width="18" height="22" rx="1"/><path d="M5 8h18"/><circle cx="14" cy="17" r="5"/></svg>Wäscheservice</div>
  <div class="service" style="left:141px;top:290px"><svg viewBox="0 0 28 28" fill="none" stroke="var(--red)" stroke-width="1.6"><path d="M14 24C4 17 3 11 6 7c3-3 6-2 8 1 2-3 5-4 8-1 3 4 2 10-8 17z"/></svg>Alltagsbegleitung</div>
</section>

<!-- Termin -->
<section class="panel p-termin">
  <div class="photo" role="img" aria-label="Foto zweier offener Hände, die ein Herz mit einem älteren Paar halten" style="left:0;top:0;width:100%;height:190px;background:linear-gradient(180deg,#a9c6d6,#d7e4ec 65%,#ffffff)"></div>
  <div class="tv" style="left:61px;top:129px;width:96px;height:56px">TV</div>
  <div class="cta">Buchen Sie gleich einen Termin:</div>
  <div class="phone">0711 98 76 54 32</div>
  <div class="url">www.lindwerk.de</div>
  <svg class="shape" style="bottom:0;height:80px" viewBox="0 0 218 80" preserveAspectRatio="none">
    <polygon points="0,30 80,80 0,80" fill="var(--red)"/>
    <polygon points="60,80 218,0 218,80" fill="var(--red)"/>
    <polygon points="120,80 218,38 218,80" fill="var(--ink)"/>
  </svg>
</section>

<svg class="glass-line" width="1200" height="813" aria-hidden="true">
  <line x1="420" y1="712" x2="472" y2="770" stroke="#7a1f4a" stroke-width="1.2"/>
</svg>
<div class="glass-note">Transparentes Glas</div>

</body>
</html>
```